Lorvex Tilo medical cannibis cultivation company

tag - Tilo rise
Lorvex Tilo medical cannabis cultivation - logo is selected- can we please see bold examples with our selection. We are mainly dealing with medical companies and professionals. We would like to be stand out in the crowd with our designs. Welcome any and all attempts. Thanks

Target Market(s)

Medical and Professional

Industry/Entity Type

Medical And Science

Font styles to use
Sans Serif

Colors

Designer to choose colors to be used in the design.

Requirements
Must have
• Bright colour and be bold- Love the teal and magenta that is currently on the dark background design.
Nice to have
• shading and the 3D affect- The shadowed appearance.
Should not have
• Anything related to illegal activity or un professional manners

```html
<!DOCTYPE html>
<html lang="en">
<head>
<meta charset="utf-8">
<title>Lorvex Tilo — Business Card</title>
<link rel="stylesheet" href="https://fonts.googleapis.com/css2?family=Cinzel:wght@400&family=Roboto+Condensed:wght@300;400;700&display=swap">
<style>
  :root {
    --backdrop: #cbbb9f;
    --card-black: #101012;
    --card-black-hi: #232327;
    --teal: #17b3e6;
    --magenta: #a34aa6;
    --back-purple: #9c47a1;
    --back-edge: #6d2c72;
    --ink-light: #e4e4e8;
    --rule: #6a6a70;
  }
  * { margin: 0; padding: 0; box-sizing: border-box; }
  html, body { width: 1200px; height: 1040px; overflow: hidden; }
  body {
    background: var(--backdrop);
    position: relative;
    font-family: "Roboto Condensed", sans-serif;
  }
  .card {
    position: absolute;
    width: 640px;
    height: 366px;
    border-radius: 22px;
    overflow: hidden;
  }

  /* Front */
  .card-front {
    left: 80px; top: 90px;
    background: linear-gradient(160deg, var(--card-black-hi) 0%, var(--card-black) 55%);
    box-shadow: 0 6px 0 -1px var(--magenta), 0 18px 30px rgba(0,0,0,0.35);
  }
  .front-tab {
    position: absolute; left: 0; top: 150px;
    width: 8px; height: 30px; background: var(--teal);
  }
  .holder-name {
    position: absolute; left: 44px; top: 58px;
    font-family: "Cinzel", serif; font-weight: 400;
    font-size: 30px; color: var(--teal); letter-spacing: 0.5px;
    white-space: nowrap;
  }
  .holder-title {
    position: absolute; left: 46px; top: 96px;
    font-size: 17px; color: var(--magenta); letter-spacing: 0.5px;
  }
  .front-rule {
    position: absolute; left: 44px; top: 124px;
    width: 420px; height: 1px; background: var(--rule);
  }
  .brand {
    position: absolute; right: 34px; top: 48px;
    display: flex; align-items: center; gap: 12px;
  }
  .brand-dot {
    width: 18px; height: 18px; border-radius: 50%; background: var(--magenta);
  }
  .brand-name {
    font-family: "Roboto Condensed", sans-serif; font-weight: 700;
    font-size: 30px; color: var(--teal); line-height: 1; white-space: nowrap;
  }
  .address {
    position: absolute; right: 34px; top: 170px;
    font-style: normal;
    text-align: right; font-size: 16px; line-height: 1.35; color: var(--ink-light);
  }
  .contacts {
    position: absolute; left: 140px; top: 196px;
    list-style: none; font-size: 16px; line-height: 1.45; color: var(--ink-light);
  }
  .contacts li { display: flex; align-items: center; gap: 10px; }
  .contacts svg { width: 13px; height: 13px; fill: var(--teal); flex: none; }
  .front-band { position: absolute; left: 0; bottom: 0; width: 640px; height: 60px; }
  .band-site {
    position: absolute; right: 30px; bottom: 16px;
    font-size: 16px; color: #fff; letter-spacing: 0.3px;
  }

  /* Back */
  .card-back {
    left: 480px; top: 590px;
    background: var(--back-purple);
    box-shadow: 0 6px 0 -1px var(--back-edge), 0 18px 30px rgba(0,0,0,0.35);
  }
  .back-brand {
    position: absolute; right: 44px; bottom: 56px;
    color: #fff; text-align: right;
  }
  .back-name {
    font-family: "Roboto Condensed", sans-serif; font-weight: 700;
    font-size: 54px; line-height: 1; white-space: nowrap;
  }
  .back-site {
    margin-top: 14px; font-size: 17px; font-weight: 300; letter-spacing: 0.5px;
  }
</style>
</head>
<body>

<section class="card card-front" aria-label="Business card front">
  <div class="front-tab"></div>
  <h1 class="holder-name">MAREK OLDEN</h1>
  <p class="holder-title">CEO/FOUNDER</p>
  <div class="front-rule"></div>

  <div class="brand">
    <span class="brand-dot"></span>
    <div class="brand-name">LORVEX TILO</div>
  </div>

  <address class="address">
    4120 Fernhill Road<br>Halden Bay, Oregon 97310
  </address>

  <ul class="contacts">
    <li><svg viewBox="0 0 16 16"><path d="M3 1l3 3-2 2c1 2 3 4 5 5l2-2 3 3-2 3C7 15 1 9 1 3z"/></svg>555 210 4471</li>
    <li><svg viewBox="0 0 16 16"><path d="M2 3h12v8H2zM5 13h6v1H5z"/></svg>555 318 2096</li>
    <li><svg viewBox="0 0 16 16"><path d="M4 1h8v14H4zM6 3v9h4V3z"/></svg>555 742 6130</li>
    <li><svg viewBox="0 0 16 16"><path d="M1 3h14v10H1zM2 4l6 5 6-5"/></svg>marek@lorvextilo.com</li>
  </ul>

  <svg class="front-band" viewBox="0 0 640 60" preserveAspectRatio="none" aria-hidden="true">
    <path d="M0 44 H405 L425 10 H640 V60 H0 Z" fill="var(--magenta)"/>
    <path d="M0 50 H410 L430 16 H640 V60 H0 Z" fill="var(--teal)"/>
  </svg>
  <div class="band-site">www.lorvextilo.com</div>
</section>

<section class="card card-back" aria-label="Business card back">
  <div class="back-brand">
    <div class="back-name">LORVEX TILO</div>
    <div class="back-site">www.lorvextilorise.com</div>
  </div>
</section>

</body>
</html>
```